Letterhead Design for Law Firm

**Edit: I have added the photo of a bottom that I like.

------
We are looking for a re-design of our new letterhead. The letterhead is for a law firm and will be used for digital and traditionally printed correspondence.

Here are some suggestions:

- Please use colours are #8ec900 and simple black.
- Please do not use any type of "waves" at the bottom of the page. This is not in style at all.
- Please stay modern yet conservative.
- Please use font Segoe UI Light or similar if you can
- Avoid clipart or illustrations.
- Utilize ample white space in the layout so the design looks clean and information is easy to read at a glance. Don't overcrowd the letterhead.
- Make sure the letterhead design is consistent with our brand identity (see corvelith.ca)
-Please, no black headers or footers.

I am attaching my current letterhead and signature for your convenience.

Remember, the letterhead is an extension of our professional identity. We are a successful firm and trial lawyers who correspond with insurers, judges, lawyers, courts, clients, etc. Make it new, modern, attractive, yet powerful and conservative.

It needs to be easily printable. I would like the bleed removed in print so the black bar the bottom crosses the page (but the text is not near the edges)
Updates

Low design quality

Target Market(s)

Clients, Government Offices, Judiciary, Lawyers, Insurance Companies, Colleagues.

Industry/Entity Type

Law

Other font styles liked:
• Segoe UI LIght, Calibri Light,

Colors
00AB8E
00BBA5
67D7C9
C6EFE9
E9F9F6

Requirements
Must have
• Everything that is on the letterhead now.
Nice to have
• Cutting Edge design, yet conservative.
Should not have
• law firm cliche design, images,

```html
<!DOCTYPE html>
<html lang="en">
<head>
<meta charset="utf-8">
<title>Ashcroft Personal Injury Lawyers – Letterhead</title>
<link href="https://fonts.googleapis.com/css2?family=Open+Sans:wght@300;400;600;700&display=swap" rel="stylesheet">
<style>
  :root {
    --brand-green: #8ec900;
    --ink: #111111;
    --paper: #ffffff;
    --backdrop: #d4d4d4;
    --signature-tone: #2a2a2a;
  }
  * { margin: 0; padding: 0; box-sizing: border-box; }
  html, body { width: 1200px; height: 686px; overflow: hidden; }
  body {
    background: var(--backdrop);
    font-family: "Open Sans", "Segoe UI", sans-serif;
    color: var(--ink);
    position: relative;
  }
  .letterhead {
    position: absolute;
    left: 352px; top: 23px;
    width: 495px; height: 640px;
    background: var(--paper);
    overflow: hidden;
    font-size: 8px;
    line-height: 10.5px;
  }

  /* Masthead */
  .masthead {
    position: absolute; left: 55px; top: 22px;
    width: 170px;
    border-top: 1px solid var(--brand-green);
    border-bottom: 1px solid var(--brand-green);
    padding: 4px 0 3px;
    text-align: center;
  }
  .firm-name {
    font-size: 28px; line-height: 30px; font-weight: 600;
    letter-spacing: 1px;
  }
  .firm-tagline {
    font-size: 6.5px; line-height: 9px; font-weight: 600;
    letter-spacing: 1.9px;
  }

  /* Letter body */
  .letter-meta { position: absolute; left: 55px; top: 92px; width: 380px; }
  .letter-meta .bold { font-weight: 700; }
  .letter-meta p { margin-bottom: 6px; }
  .letter-meta .address { margin-bottom: 8px; }
  .re-line { display: flex; white-space: nowrap; }
  .re-line .label { width: 44px; flex: none; }
  .re-line .subject { font-weight: 700; }
  .rule {
    position: absolute; left: 50px; top: 298px;
    width: 390px; height: 1.5px; background: var(--brand-green);
  }

  /* Contact panel */
  .contact-divider {
    position: absolute; left: 342px; top: 12px;
    width: 1.5px; height: 158px; background: var(--brand-green);
  }
  .contact-panel {
    position: absolute; left: 352px; top: 16px; width: 140px;
    font-size: 7px; line-height: 9.5px;
  }
  .contact-panel .web { color: var(--brand-green); }
  .contact-panel .practice { margin-top: 7px; }

  /* Sign-off */
  .sign-off { position: absolute; left: 30px; top: 478px; width: 260px; }
  .sign-off .bold { font-weight: 700; }
  .signature {
    display: block; width: 150px; height: 34px; margin: 4px 0 4px 10px;
    background: linear-gradient(90deg, transparent, rgba(42,42,42,0.25), transparent);
  }
  .footer-curve { position: absolute; left: 0; bottom: 0; }
</style>
</head>
<body>
  <main class="letterhead">
    <header class="masthead">
      <div class="firm-name">ASHCROFT</div>
      <div class="firm-tagline">PERSONAL INJURY LAWYERS</div>
    </header>

    <section class="letter-meta">
      <p class="bold">Without Prejudice</p>
      <p>March 13, 2024</p>
      <p class="bold">By Email</p>
      <div class="address">
        Brightwater Insurance Company<br>
        Claims Litigation Department<br>
        240 Harbour Road North<br>
        P.O. Box 3100<br>
        Waterloo, ON&nbsp; N2A 7K2
      </div>
      <p>Attention:&nbsp; Mr. Owen Fairley</p>
      <p>Mr. Fairley:</p>
      <div class="re-line">
        <span class="label">Re:</span>
        <span class="subject">Harlow v. Penrose et al.<br>DOL: September 12, 2019<br>Pre-Mediation Settlement Proposal – March 13th, 2024</span>
      </div>
    </section>
    <div class="rule"></div>

    <div class="contact-divider"></div>
    <aside class="contact-panel">
      <div class="web">www.CORVELITH.ca</div>
      <div>18 Elm Street E., Suite 902<br>Hamilton, ON L8R 2B6<br>T: 905-555-0142<br>F: 905-555-0187<br>File Clerk: Clara Whitmore<br>Email: clara@corvelith.ca</div>
      <div class="practice">Practice Restricted<br>Serious Personal Injury<br>Wrongful Death Litigation<br>Long-Term Disability Litigation<br>Wrongful Dismissal Litigation<br>Employee Terminations</div>
    </aside>

    <section class="sign-off">
      <div class="bold">Yours very truly,</div>
      <div class="bold">ASHCROFT PERSONAL INJURY LAWYERS</div>
      <span class="signature" role="img" aria-label="Handwritten signature of Daniel R. Ashcroft"></span>
      <div>Daniel R. Ashcroft</div>
      <div class="bold">Ashcroft Law Professional Corporation</div>
      <div>/cw</div>
      <div>Encl.</div>
    </section>

    <svg class="footer-curve" width="495" height="60" viewBox="0 0 495 60" aria-hidden="true">
      <path d="M0 2 Q220 40 430 60 L0 60 Z" fill="var(--brand-green)"/>
      <path d="M0 12 Q240 44 470 60 L0 60 Z" fill="var(--paper)"/>
      <path d="M60 60 Q300 30 495 40 L495 60 Z" fill="var(--ink)"/>
      <path d="M40 60 Q280 42 430 60 Z" fill="var(--paper)"/>
    </svg>
  </main>
</body>
</html>
```